Velk Partners Building Business Cards

We need a business card that reflects our business as "Solar Experts" in San Diego. Browse our website www.velkpartners.example our License needs to be displayed as "CSLB# 3867140" our phone number is (619) 555-0187

Save thousands on your electric bills and increase the value of your home while helping to protect the environment. Our solar installation experts will help you design the system that's right for you, using only the highest quality equipment that will look great and give you ideal performance. Our goal is to make you energy independent, and get your electric bill to 0.

Paul Osterby
(619) 555-0187
paul@velkpartners.example

Target Market(s)

Home owners in san diego looking for solar

Industry/Entity Type

Solar Energy

Contact Information for Business Card

Paul Osterby
(619) 555-0187
paul@velkpartners.example

Font styles to use
Other font styles liked:
• Use our logo font

Requirements
Must have
• License needs to be displayed as "CSLB# 3867140" our phone number is (619) 555-0187
Nice to have
• Real images of rooftop home solar in san diego
Should not have
• our business address

```html
<!DOCTYPE html>
<html lang="en">
<head>
<meta charset="utf-8">
<title>Velk Partners Building — Business Card</title>
<link rel="stylesheet" href="https://fonts.googleapis.com/css2?family=Cinzel:wght@400;600&family=Montserrat:wght@700;800&display=swap">
<style>
  :root {
    --navy: #124a86;
    --navy-text: #1d4a86;
    --gold: #f7ae1c;
    --white: #ffffff;
    --stage: #e9eaec;
    --panel-dark: #1d2f5c;
    --panel-mid: #3d5d94;
    --roof: #8a8378;
  }
  * { box-sizing: border-box; margin: 0; padding: 0; }
  html, body { width: 1200px; height: 900px; overflow: hidden; }
  body {
    background: var(--stage);
    position: relative;
    font-family: "Cinzel", serif;
  }
  .card {
    position: absolute;
    width: 620px;
    height: 354px;
    border-radius: 22px;
    overflow: hidden;
    box-shadow: 0 14px 30px rgba(0,0,0,.18);
  }

  /* Front: rooftop solar photo */
  .card-front { left: 90px; top: 80px; }
  .card-front .photo {
    position: absolute; inset: 0;
    background:
      linear-gradient(120deg, rgba(95,140,80,.9) 0%, rgba(95,140,80,0) 22%),
      linear-gradient(200deg, var(--roof) 0%, var(--roof) 18%, var(--panel-mid) 38%, var(--panel-dark) 70%, #2a3448 100%);
  }
  .card-front .brand {
    position: absolute; left: 0; right: 0; top: 130px;
    display: flex; align-items: center; justify-content: center; gap: 14px;
  }
  .card-front .brand-dot {
    width: 34px; height: 34px; border-radius: 50%; background: var(--gold);
  }
  .card-front .brand-name {
    font-family: "Montserrat", sans-serif; font-weight: 800;
    font-size: 36px; color: var(--white);
  }
  .card-front .web {
    position: absolute; right: 60px; bottom: 62px;
    font-size: 14px; color: var(--white); letter-spacing: .5px;
  }

  /* Back: contact side */
  .card-back { left: 490px; top: 450px; background: var(--white); }
  .card-back .waves { position: absolute; inset: 0; }
  .card-back .logo {
    position: absolute; left: 40px; top: 96px;
  }
  .card-back .logo-name {
    font-family: "Montserrat", sans-serif; font-weight: 800;
    font-size: 28px; color: var(--white); line-height: 1;
  }
  .card-back .license {
    margin-top: 10px;
    font-size: 15px; color: var(--gold); letter-spacing: .5px;
  }
  .card-back .contact {
    position: absolute; right: 24px; top: 225px;
    list-style: none; text-align: right;
  }
  .card-back .contact li {
    display: flex; align-items: center; justify-content: flex-end; gap: 7px;
    font-size: 11px; color: var(--navy-text); line-height: 18px;
    text-transform: uppercase; white-space: nowrap;
  }
  .card-back .contact li.phone { text-transform: none; }
  .card-back .contact svg { width: 10px; height: 10px; flex: none; }
  .card-back .holder {
    position: absolute; left: 36px; bottom: 30px;
    font-family: "Montserrat", sans-serif; font-weight: 700;
    font-size: 24px; color: var(--navy-text);
  }
  .card-back .corner-dot {
    position: absolute; left: -14px; bottom: 24px;
    width: 30px; height: 30px; border-radius: 50%; background: var(--gold);
  }
</style>
</head>
<body>

  <section class="card card-front">
    <div class="photo" role="img" aria-label="Photograph of rooftop solar panels on a San Diego home"></div>
    <div class="brand">
      <span class="brand-dot"></span>
      <span class="brand-name">Velk Partners Building</span>
    </div>
    <p class="web">WWW.VELKPARTNERS.EXAMPLE</p>
  </section>

  <section class="card card-back">
    <svg class="waves" viewBox="0 0 620 354" preserveAspectRatio="none" aria-hidden="true">
      <path fill="var(--navy)" d="M0,0 H620 V50 C470,55 400,100 350,170 C300,230 200,245 0,232 Z"/>
      <path fill="var(--gold)" d="M0,232 C200,245 300,230 350,170 C400,100 470,55 620,50 V74 C490,78 420,120 375,180 C320,245 210,262 0,250 Z"/>
      <path fill="var(--gold)" d="M140,262 C300,266 370,240 405,190 C440,135 500,96 620,90 V108 C515,110 460,140 425,190 C390,240 330,276 140,266 Z"/>
    </svg>

    <div class="logo">
      <p class="logo-name">Velk Partners Building</p>
      <p class="license">CSLB# 3867140</p>
    </div>

    <ul class="contact">
      <li class="phone">(619) 555-0187
        <svg viewBox="0 0 12 12"><path fill="var(--gold)" d="M2.4 1 L4.4 1 L5 3.6 L3.8 4.6 C4.4 6 5.6 7.4 7.2 8.2 L8.3 7 L11 7.6 L11 9.6 C11 10.4 10.3 11 9.5 11 C5 10.6 1.4 7 1 2.5 C1 1.7 1.6 1 2.4 1 Z"/></svg>
      </li>
      <li>paul@velkpartners.example
        <svg viewBox="0 0 12 12"><rect x="1" y="2.5" width="10" height="7" rx="1" fill="none" stroke="var(--gold)" stroke-width="1.3"/><path d="M1.5 3 L6 6.5 L10.5 3" fill="none" stroke="var(--gold)" stroke-width="1.2"/></svg>
      </li>
      <li>www.velkpartners.example
        <svg viewBox="0 0 12 12"><circle cx="6" cy="6" r="5" fill="var(--gold)"/><path d="M1 6 H11 M6 1 C3.5 3.5 3.5 8.5 6 11 M6 1 C8.5 3.5 8.5 8.5 6 11" fill="none" stroke="var(--white)" stroke-width=".8"/></svg>
      </li>
    </ul>

    <span class="corner-dot"></span>
    <p class="holder">Paul Osterby</p>
  </section>

</body>
</html>
```